Local Flower Farm Needs Business Card Design

I need business cards designed for a flower farm based in Eudora, Kansas.
Business Info:
We are a local cut flower farm located in Eudora, Kansas, founded by Corinne Haldwick. What started as a passion for agriculture and search for more joy in daily life has blossomed into a small business dedicated to providing the community with beautiful, fresh, and sustainable flowers. We specialize in local, seasonal blooms, ensuring that every petal reflects the care and dedication we pour into our craft. Our mission is to deliver the highest quality flowers directly to our customers through local farmers markets and to florists who share our commitment to sustainability. Join us in celebrating the beauty of nature, one bloom at a time!
Contact Details:
Corinne Haldwick
Owner
Phone 913-555-0147
Facebook: Rosalind Thorpe Gardens
Instagram: @RosalindThorpeGardens
Website: RosalindThorpeGardens.example
Target Market(s)
Wholesale to Florists and Direct to Consumer via Farmers Market
Industry/Entity Type
Florist, Farm
Contact Information for Business Card
Name, Contact Info, Logo
Look and feel
Each slider illustrates characteristics of the customer's brand and the style your logo design should communicate.

```html
<!DOCTYPE html>
<html lang="en">
<head>
<meta charset="utf-8">
<title>Rosalind Thorpe Gardens – Business Cards</title>
<link rel="stylesheet" href="https://fonts.googleapis.com/css2?family=Montserrat:wght@400;700&display=swap">
<style>
  :root {
    --bg: #161616;
    --card-dark: #0e2528;
    --card-light: #2d4a4f;
    --ink: #ffffff;
    --ink-soft: #e6eeee;
    --emboss: #3a585c;
    --emboss-line: #45666a;
  }
  * { box-sizing: border-box; margin: 0; padding: 0; }
  html, body {
    width: 1200px; height: 900px; overflow: hidden;
    background: var(--bg);
    font-family: "Montserrat", sans-serif;
  }
  .sheet {
    width: 1200px; height: 900px;
    display: flex; flex-direction: column; align-items: center; justify-content: center;
    gap: 36px;
  }
  .card {
    width: 700px; height: 400px;
    position: relative;
    background: linear-gradient(120deg, var(--card-dark) 0%, #163338 50%, var(--card-light) 100%);
    box-shadow: 0 12px 30px rgba(0,0,0,.55);
  }
  /* Front */
  .front-mark {
    position: absolute; left: 50%; top: 50%;
    width: 270px; height: 270px; transform: translate(-50%, -50%);
    border: 1.5px solid var(--emboss-line); border-radius: 50%;
    display: flex; align-items: center; justify-content: center; text-align: center;
  }
  .front-mark .brand-name {
    color: var(--emboss);
    font-size: 26px; font-weight: 400; line-height: 1.3; letter-spacing: 3px;
    text-transform: uppercase;
  }
  /* Back */
  .contact {
    position: absolute; left: 52px; top: 46px;
    color: var(--ink);
  }
  .person-name { font-size: 23px; font-weight: 700; letter-spacing: 1.5px; text-transform: uppercase; }
  .person-role { font-size: 13px; font-weight: 400; letter-spacing: 1px; margin-top: 2px; }
  .address { font-size: 14px; line-height: 1.3; margin-top: 26px; color: var(--ink-soft); }
  .lines { list-style: none; margin-top: 20px; font-size: 14px; }
  .lines li { display: flex; align-items: center; gap: 10px; margin-bottom: 6px; }
  .lines svg { width: 14px; height: 14px; flex: none; }
  .divider { width: 12px; height: 1.5px; background: var(--ink); margin: 6px 0 16px; }
  .social-dot { width: 12px; height: 12px; flex: none; border: 1.5px solid var(--ink); }
  .social-dot.round { border-radius: 50%; }
  .back-mark {
    position: absolute; right: 52px; top: 50%;
    width: 270px; height: 270px; transform: translateY(-50%);
    border: 1.5px solid var(--ink); border-radius: 50%;
    display: flex; align-items: center; justify-content: center; text-align: center;
  }
  .back-mark .brand-name {
    color: var(--ink);
    font-size: 26px; font-weight: 400; line-height: 1.3; letter-spacing: 3px;
    text-transform: uppercase;
  }
</style>
</head>
<body>
<main class="sheet">
  <section class="card card-front" aria-label="Card front">
    <div class="front-mark">
      <p class="brand-name">Rosalind<br>Thorpe<br>Gardens</p>
    </div>
  </section>

  <section class="card card-back" aria-label="Card back">
    <div class="contact">
      <h1 class="person-name">Corinne Haldwick</h1>
      <p class="person-role">OWNER</p>
      <p class="address">4820 Meadowlark Ln<br>Unit 12<br>Eudora, KS 66025</p>
      <ul class="lines">
        <li>
          <svg viewBox="0 0 24 24" fill="#fff" aria-hidden="true"><path d="M6.6 10.8a15 15 0 0 0 6.6 6.6l2.2-2.2a1 1 0 0 1 1-.25 11.4 11.4 0 0 0 3.6.57 1 1 0 0 1 1 1V20a1 1 0 0 1-1 1A17 17 0 0 1 3 4a1 1 0 0 1 1-1h3.5a1 1 0 0 1 1 1c0 1.25.2 2.45.57 3.57a1 1 0 0 1-.25 1z"/></svg>
          913-555-0147
        </li>
        <li>
          <svg viewBox="0 0 24 24" fill="#fff" aria-hidden="true"><path d="M2 5h20v14H2z" opacity=".0"/><path d="M3 5h18a1 1 0 0 1 1 1v12a1 1 0 0 1-1 1H3a1 1 0 0 1-1-1V6a1 1 0 0 1 1-1zm9 7.5L20 7H4z"/></svg>
          info@RosalindThorpeGardens.example
        </li>
        <li>
          <svg viewBox="0 0 24 24" fill="none" stroke="#fff" stroke-width="2" aria-hidden="true"><circle cx="12" cy="12" r="9"/><path d="M3 12h18M12 3c3 3 3 15 0 18M12 3c-3 3-3 15 0 18"/></svg>
          www.RosalindThorpeGardens.example
        </li>
      </ul>
      <div class="divider"></div>
      <ul class="lines">
        <li><span class="social-dot round"></span>Rosalind Thorpe Gardens</li>
        <li><span class="social-dot"></span>@RosalindThorpeGardens</li>
      </ul>
    </div>
    <div class="back-mark">
      <p class="brand-name">Rosalind<br>Thorpe<br>Gardens</p>
    </div>
  </section>
</main>
</body>
</html>
```